MRT Property - Business Cards

Looking for a business card & general letterhead, signage etc design for our new logo.

Colours:
000a20
0056a2
00b5ef
0088ce
68cef2

Fonts:
Poppins
Karla

Please keep look and feel of new brand - example in the zip package I sent.

```html
<!DOCTYPE html>
<html lang="en">
<head>
<meta charset="utf-8">
<title>MRT Property – Business Cards</title>
<link rel="stylesheet" href="https://fonts.googleapis.com/css2?family=Poppins:wght@400;500;600;700&display=swap">
<style>
  :root {
    --stage: #222222;
    --card: #0f1426;
    --navy: #000a20;
    --brand-blue: #0056a2;
    --mid-blue: #0088ce;
    --cyan: #00b5ef;
    --sky: #68cef2;
    --ink-light: #e9eef5;
  }
  * { box-sizing: border-box; margin: 0; padding: 0; }
  html, body {
    width: 1200px; height: 780px; overflow: hidden;
    background: var(--stage);
    font-family: "Poppins", sans-serif;
  }
  .sheet {
    position: relative; width: 1200px; height: 780px;
    display: flex; align-items: center; justify-content: center; gap: 60px;
  }
  .card {
    position: relative; width: 520px; height: 316px;
    background: var(--card); overflow: hidden;
    box-shadow: 0 18px 40px rgba(0,0,0,.45);
  }
  .card-swoosh { position: absolute; inset: 0; width: 100%; height: 100%; }

  .brand-name {
    position: absolute; font-weight: 700; color: var(--brand-blue);
    letter-spacing: .5px; line-height: 1;
  }
  .card-front .brand-name { top: 40px; left: 74px; font-size: 30px; }
  .card-back .brand-name { right: 40px; bottom: 40px; font-size: 30px; }

  .contact-list {
    position: absolute; top: 112px; left: 30px; list-style: none;
    font-size: 11px; color: var(--ink-light); line-height: 1;
  }
  .contact-list li { display: flex; align-items: center; gap: 8px; margin-bottom: 7px; }
  .contact-icon { width: 11px; height: 11px; flex: none; }

  .holder {
    position: absolute; top: 54px; right: 38px; text-align: right;
  }
  .holder-name { font-size: 26px; font-weight: 600; line-height: 1.05; }
  .holder-first { color: var(--brand-blue); }
  .holder-last { color: var(--sky); font-weight: 500; }
  .holder-role { font-size: 13px; color: var(--ink-light); margin-top: 2px; }
  .holder-marker {
    position: absolute; top: 56px; right: 0; width: 22px; height: 44px;
    background: var(--sky);
  }

  .address {
    position: absolute; right: 52px; top: 178px; text-align: right;
    font-size: 13px; line-height: 1.45; color: var(--ink-light);
  }
</style>
</head>
<body>
<main class="sheet">

  <section class="card card-front" aria-label="Business card front">
    <svg class="card-swoosh" viewBox="0 0 520 316" aria-hidden="true">
      <path d="M0 222 C120 246 240 276 300 316 L0 316 Z" fill="var(--brand-blue)"/>
      <path d="M0 170 C120 200 250 250 330 316 L306 316 C230 262 120 220 0 200 Z" fill="var(--sky)"/>
    </svg>

    <div class="brand-name">MRT Property</div>

    <ul class="contact-list">
      <li>
        <svg class="contact-icon" viewBox="0 0 12 12" aria-hidden="true"><path d="M2.5 1 L4.5 1 L5.2 3.4 L4 4.4 C4.6 5.8 6.2 7.4 7.6 8 L8.6 6.8 L11 7.5 L11 9.5 C11 10.3 10.3 11 9.5 11 C5 11 1 7 1 2.5 C1 1.7 1.7 1 2.5 1 Z" fill="var(--cyan)"/></svg>
        +61 2 9000 1234
      </li>
      <li>
        <svg class="contact-icon" viewBox="0 0 12 12" aria-hidden="true"><circle cx="6" cy="6" r="5" fill="none" stroke="var(--cyan)" stroke-width="1.2"/><ellipse cx="6" cy="6" rx="2.2" ry="5" fill="none" stroke="var(--cyan)" stroke-width="1"/><line x1="1" y1="6" x2="11" y2="6" stroke="var(--cyan)" stroke-width="1"/></svg>
        www.mrtproperty.com.au
      </li>
      <li>
        <svg class="contact-icon" viewBox="0 0 12 12" aria-hidden="true"><rect x="1" y="2.5" width="10" height="7" fill="none" stroke="var(--cyan)" stroke-width="1.2"/><path d="M1 2.5 L6 6.5 L11 2.5" fill="none" stroke="var(--cyan)" stroke-width="1.1"/></svg>
        info@mrtproperty.com.au
      </li>
    </ul>

    <div class="holder">
      <div class="holder-name"><span class="holder-first">Callum</span> <span class="holder-last">Reid</span></div>
      <div class="holder-role">Director</div>
    </div>
    <div class="holder-marker"></div>

    <address class="address" style="font-style:normal">
      Suite 4.12, Level 3<br>
      18 Ridgeway Lane<br>
      Riverside Park NSW 2199
    </address>
  </section>

  <section class="card card-back" aria-label="Business card back">
    <div class="brand-name">MRT Property</div>
  </section>

</main>
</body>
</html>
```